Business Card for Field Bloom-Eco Friendly Organic Clothing Brand

We are looking for an amazing business card for our eco friendly, organic clothing brand. We are thinking maybe a business card with a peel off sticker on the back, since our hanging clothing tag is a peel off sticker on the back. I will attach our hang tag so we can make sure we stay in line with our design. I've also attached a bag we are doing because I do like the scattered emblem look as well.

```html
<!DOCTYPE html>
<html lang="en">
<head>
<meta charset="utf-8">
<title>Field Bloom — Business Card</title>
<link rel="stylesheet" href="https://fonts.googleapis.com/css2?family=Open+Sans:wght@400;600&display=swap">
<style>
  :root {
    --backdrop: #e8e5e0;
    --card-light: #ffffff;
    --card-shade: #ececec;
    --brand-pink: #e0119b;
    --brand-green: #1f8a4c;
    --ink: #2b2b2b;
  }
  * { box-sizing: border-box; margin: 0; padding: 0; }
  html, body {
    width: 1200px; height: 892px; overflow: hidden;
    background: var(--backdrop);
    font-family: "Open Sans", Arial, sans-serif;
  }
  .sheet {
    position: relative; width: 1200px; height: 892px;
    display: flex; align-items: center; justify-content: center; gap: 40px;
  }
  .card {
    position: relative; width: 520px; height: 297px;
    border-radius: 18px;
    background: linear-gradient(135deg, var(--card-light) 0%, var(--card-shade) 100%);
    box-shadow: 0 6px 18px rgba(0,0,0,0.18);
    overflow: hidden;
  }
  /* Front */
  .brand-lockup {
    position: absolute; left: 40px; top: 62px;
    display: flex; align-items: center; gap: 12px;
  }
  .brand-mark {
    width: 22px; height: 22px; border-radius: 50%;
    background: var(--brand-green);
  }
  .brand-name {
    font-weight: 600; font-size: 38px; color: var(--brand-pink);
    letter-spacing: 0.5px; line-height: 1;
  }
  .divider {
    position: absolute; left: 0; top: 150px; width: 355px; height: 2px;
    background: var(--brand-pink);
  }
  .person {
    position: absolute; left: 365px; top: 118px;
  }
  .person-name {
    font-weight: 600; font-size: 24px; color: var(--brand-green); line-height: 1.1;
  }
  .person-title {
    font-size: 14px; color: var(--ink); text-align: right; margin-top: 2px;
  }
  .contact-list {
    position: absolute; left: 40px; top: 176px;
    list-style: none; display: flex; flex-direction: column; gap: 10px;
  }
  .contact-item {
    display: flex; align-items: center; gap: 12px;
    font-size: 17px; color: var(--ink);
  }
  .contact-icon { width: 15px; height: 15px; flex: none; }
  /* Back */
  .card-back { display: flex; align-items: center; justify-content: center; }
  .card-back .brand-name { font-size: 60px; }
  .card-back .brand-lockup { position: static; gap: 16px; }
  .card-back .brand-mark { width: 30px; height: 30px; }
</style>
</head>
<body>
<main class="sheet">
  <section class="card card-front" aria-label="Card front">
    <div class="brand-lockup">
      <span class="brand-mark"></span>
      <span class="brand-name">Field Bloom</span>
    </div>
    <div class="divider"></div>
    <div class="person">
      <p class="person-name">Dana Reyes</p>
      <p class="person-title">President</p>
    </div>
    <ul class="contact-list">
      <li class="contact-item">
        <svg class="contact-icon" viewBox="0 0 16 16" aria-hidden="true">
          <rect width="16" height="16" fill="#1f8a4c"/>
          <path d="M5 3.5 L6.5 3.5 L7.3 6 L6.2 7 Q7.2 9 9 9.8 L10 8.7 L12.5 9.5 L12.5 11 Q12.5 12.5 11 12.5 Q4 12 3.5 5 Q3.5 3.5 5 3.5 Z" fill="#fff"/>
        </svg>
        (555) 014-2290
      </li>
      <li class="contact-item">
        <svg class="contact-icon" viewBox="0 0 16 16" aria-hidden="true">
          <rect width="16" height="16" fill="#1f8a4c"/>
          <path d="M8 2.5 Q11.5 2.5 11.5 6 Q11.5 8.5 8 13 Q4.5 8.5 4.5 6 Q4.5 2.5 8 2.5 Z" fill="#fff"/>
          <circle cx="8" cy="6" r="1.4" fill="#1f8a4c"/>
        </svg>
        Palm Cove, FL&nbsp; 33410
      </li>
      <li class="contact-item">
        <svg class="contact-icon" viewBox="0 0 16 16" aria-hidden="true">
          <rect width="16" height="16" fill="#1f8a4c"/>
          <rect x="3" y="4.5" width="10" height="7" fill="#fff"/>
          <path d="M3 4.5 L8 8.5 L13 4.5" fill="none" stroke="#1f8a4c" stroke-width="1"/>
        </svg>
        hello@fieldbloom.com
      </li>
    </ul>
  </section>

  <section class="card card-back" aria-label="Card back">
    <div class="brand-lockup">
      <span class="brand-mark"></span>
      <span class="brand-name">Field Bloom</span>
    </div>
  </section>
</main>
</body>
</html>
```